Bright Towns Forum PowerPoint Design Template and Sample Deck

The Bright Towns Forum is an international organization that seeks to improve the livability, workability and sustainability of the world’s cities.
We seek a versatile PowerPoint design template with 10 slide types plus a “self-documenting” sample deck. Your design will be used in keynote speeches and workshops around the world.
After the contest is completed, we will ask the winning designer to add 10-20 additional slide types for $75 per slide. We also seek a long-term relationship whereby we can request “custom” slides and/or ask the designer to touch up the slides we build to make them better.
FILES. We have uploaded several files:
2. PALETTE. Shows our official colors.
3 LOGOS. Several individual files with different variations of our logo. Some with our motto, some without.
2. SAMPLE SLIDES. Because we were unable to successfully upload our sample deck, we are making it available via this FileNook link:
https://www.filenook-example.com/s/k7qrtmzp2wd9hxa/The%20Bright%20Towns%20Forum%20Design%20Contest%20Notes.docx?dl=0
Target Market(s)
Mayors, department heads, CIOs, senior executives from technology companies
Industry/Entity Type
Information Technology
Colors
Designer to choose colors to be used in the design.
Requirements
Must have
- Please see uploaded Word document for requirements, nice to haves and should not haves and uploaded palette for color preferences.
Nice to have
- see above
Should not have
- see above

```html
<!DOCTYPE html>
<html lang="en">
<head>
<meta charset="utf-8">
<title>Agenda</title>
<link rel="stylesheet" href="https://fonts.googleapis.com/css2?family=Open+Sans:wght@700&family=Carlito:wght@400;700&display=swap">
<style>
:root{
  --navy:#002b5c;
  --item:#1f4478;
  --photo-top:#5f7d9c;
  --photo-mid:#4a6a8c;
  --photo-low:#2a4a6c;
  --white:#ffffff;
}
*{margin:0;padding:0;box-sizing:border-box}
html,body{width:1200px;height:675px;overflow:hidden;background:var(--white)}
.slide{position:relative;width:1200px;height:675px;background:var(--white);overflow:hidden}
.hero-photo{
  position:absolute;left:0;top:0;width:428px;height:675px;
  background:linear-gradient(160deg,var(--photo-top) 0%,var(--photo-mid) 45%,var(--photo-low) 75%,var(--photo-mid) 100%);
}
.vertical-title{
  position:absolute;left:188px;top:72px;width:60px;
  display:flex;flex-direction:column;align-items:center;gap:0;
  font-family:"Open Sans",sans-serif;font-weight:700;font-size:58px;line-height:95px;color:var(--white);
  list-style:none;
}
.pointer{position:absolute;left:428px;top:195px}
.agenda-list{
  position:absolute;left:510px;top:194px;list-style:none;
  font-family:"Carlito","Calibri",sans-serif;font-size:39px;color:var(--item);
}
.agenda-list li{height:70.5px;line-height:48px}
.agenda-list .current{font-weight:700}
.page-number{
  position:absolute;left:1089px;top:623px;width:51px;height:51px;border-radius:50%;
  background:var(--navy);color:var(--white);
  font-family:Arial,sans-serif;font-size:15px;display:flex;align-items:center;justify-content:center;
}
</style>
</head>
<body>
<main class="slide">
  <div class="hero-photo" role="img" aria-label="Blurred photo of a laptop keyboard and coffee cup in blue tones"></div>
  <h1 class="vertical-title" aria-label="Agenda">
    <span>A</span><span>G</span><span>E</span><span>N</span><span>D</span><span>A</span>
  </h1>
  <svg class="pointer" width="52" height="45" viewBox="0 0 52 45" aria-hidden="true">
    <polygon points="0,0 52,22.5 0,45" fill="var(--navy)"/>
  </svg>
  <ol class="agenda-list">
    <li class="current">Agenda Item 1</li>
    <li>Agenda Item 2</li>
    <li>Agenda Item 3</li>
    <li>Agenda Item 4</li>
  </ol>
  <div class="page-number">2</div>
</main>
</body>
</html>
```